Redesign of business card for Cedar Ridge Mechanical

We are looking for a new design for our business cards for Cedar Ridge Mechanical. We are a plumbing & HVAC construction company, operating on the West Coast of Canada and USA. Logo attached.
Industry/Entity Type
Construction - Plumbing & HVAC
Contact Information for Business Card
Name, address, phone numbers, email, website address
Look and feel
Each slider illustrates characteristics of the customer's brand and the style your logo design should communicate.

```html
<!DOCTYPE html>
<html lang="en">
<head>
<meta charset="utf-8">
<title>Cedar Ridge Mechanical – Business Card</title>
<link rel="stylesheet" href="https://fonts.googleapis.com/css2?family=Poppins:wght@300;400;500;700&display=swap">
<style>
  :root {
    --backdrop: #222222;
    --card-front: #f3f3f3;
    --card-back: #e4e6e6;
    --ink: #111111;
    --ink-soft: #2a2a2a;
    --band: #e2e2e2;
    --band-shadow: rgba(0,0,0,0.18);
    --emboss: #d3d6d6;
  }
  * { box-sizing: border-box; margin: 0; padding: 0; }
  html, body { width: 1200px; height: 780px; overflow: hidden; }
  body {
    background: var(--backdrop);
    font-family: "Poppins", sans-serif;
    color: var(--ink);
    position: relative;
  }
  .card {
    position: absolute;
    top: 235px;
    width: 540px;
    height: 309px;
    border-radius: 2px;
    overflow: hidden;
  }
  .card--front { left: 40px; background: var(--card-front); }
  .card--back  { left: 620px; background: var(--card-back); display: flex; align-items: center; justify-content: center; }

  .brand {
    position: absolute;
    top: 26px; left: 0; right: 0;
    display: flex; align-items: center; justify-content: center; gap: 8px;
  }
  .brand__square { width: 16px; height: 16px; background: var(--ink); }
  .brand__name { font-weight: 700; font-size: 15px; letter-spacing: 0.06em; text-transform: uppercase; }

  .name-band {
    position: absolute;
    top: 66px; left: 0; right: 0;
    height: 62px;
    background: linear-gradient(to bottom, var(--card-front) 0%, var(--band) 55%, var(--card-front) 100%);
    box-shadow: 0 14px 22px -14px var(--band-shadow);
    text-align: center;
    padding-top: 8px;
  }
  .person { font-size: 26px; line-height: 1.1; }
  .person__first { font-weight: 700; }
  .person__last { font-weight: 300; }
  .role { font-size: 12px; font-weight: 500; margin-top: 2px; }

  .contact {
    position: absolute;
    top: 142px; left: 0; right: 0;
    text-align: center;
    font-size: 12.5px;
    line-height: 1.35;
    color: var(--ink-soft);
  }
  .contact__icons { display: flex; justify-content: center; gap: 5px; margin-bottom: 4px; }
  .icon { width: 16px; height: 16px; border-radius: 50%; background: var(--ink); display: inline-flex; align-items: center; justify-content: center; }
  .icon svg { width: 10px; height: 10px; }
  .contact__line { font-weight: 400; }
  .contact__line--light { font-weight: 300; }
  .contact__pin { margin: 10px auto 4px; }

  .back-brand { display: flex; align-items: center; gap: 14px; }
  .back-brand__square { width: 40px; height: 40px; background: var(--emboss); }
  .back-brand__name { font-weight: 700; font-size: 30px; letter-spacing: 0.05em; text-transform: uppercase; color: var(--emboss); }
</style>
</head>
<body>
  <section class="card card--front" aria-label="Business card front">
    <div class="brand">
      <span class="brand__square"></span>
      <span class="brand__name">Cedar Ridge Mechanical</span>
    </div>

    <div class="name-band">
      <p class="person"><span class="person__first">Marta</span> <span class="person__last">Kovar</span></p>
      <p class="role">Founder &amp; CEO</p>
    </div>

    <div class="contact">
      <div class="contact__icons">
        <span class="icon" aria-label="Phone">
          <svg viewBox="0 0 10 10"><path d="M2 1 L3.6 1 L4.2 3 L3.2 3.8 Q4 5.8 6.2 6.8 L7 5.8 L9 6.4 L9 8 Q8.8 9 7.8 9 Q1 8.4 1 2.2 Q1 1 2 1 Z" fill="#fff"/></svg>
        </span>
        <span class="icon" aria-label="Email">
          <svg viewBox="0 0 10 10"><rect x="1" y="2.5" width="8" height="5.5" fill="none" stroke="#fff" stroke-width="1"/><path d="M1 2.5 L5 5.8 L9 2.5" fill="none" stroke="#fff" stroke-width="1"/></svg>
        </span>
        <span class="icon" aria-label="Website">
          <svg viewBox="0 0 10 10"><circle cx="5" cy="5" r="3.8" fill="none" stroke="#fff" stroke-width="0.9"/><ellipse cx="5" cy="5" rx="1.6" ry="3.8" fill="none" stroke="#fff" stroke-width="0.8"/><path d="M1.2 5 H8.8" stroke="#fff" stroke-width="0.8"/></svg>
        </span>
      </div>
      <p class="contact__line contact__line--light">07 5128 2200</p>
      <p class="contact__line">www.cedarridgemech.com.au</p>
      <p class="contact__line">admin@cedarridgemech.com.au</p>
      <span class="icon contact__pin" aria-label="Address" style="display:flex;">
        <svg viewBox="0 0 10 10"><path d="M5 9.2 Q2 5.6 2 3.8 A3 3 0 0 1 8 3.8 Q8 5.6 5 9.2 Z" fill="#fff"/><circle cx="5" cy="3.9" r="1.1" fill="#111"/></svg>
      </span>
      <p class="contact__line contact__line--light">482 Alderwood Lane, Fairview, WI 53901</p>
    </div>
  </section>

  <section class="card card--back" aria-label="Business card back">
    <div class="back-brand">
      <span class="back-brand__square"></span>
      <span class="back-brand__name">Cedar Ridge Mechanical</span>
    </div>
  </section>
</body>
</html>
```